Business Card Design

New business card design

Target Market(s)

Residential & Commercial Property Managers

Industry/Entity Type

Plumbing Services

Contact Information for Business Card

Name - Rowan Keddle, title - Director, Phone Number - 0431 286 517, email - rowan@tbk-plumbing.com.au, Company ABN - 73 215 904 386,

Font styles to use
Sans Serif

Colors
0054AA
0677BA
7BADD7
CADEEF
E8F1F8

```html
<!DOCTYPE html>
<html lang="en">
<head>
<meta charset="utf-8">
<title>TBK Plumbing Services – Business Card</title>
<link href="https://fonts.googleapis.com/css2?family=Montserrat:wght@300;400;600;700&display=swap" rel="stylesheet">
<style>
  :root {
    --stage: #2b2b2d;
    --card: #1f242c;
    --card-edge: #2a303a;
    --blue-deep: #0054AA;
    --blue: #0677BA;
    --blue-bright: #2a9fe0;
    --blue-soft: #7BADD7;
    --ice: #CADEEF;
    --white: #f3f6f9;
    --grey: #8a9099;
  }
  * { box-sizing: border-box; margin: 0; padding: 0; }
  html, body { width: 1200px; height: 900px; overflow: hidden; }
  body {
    background: var(--stage);
    font-family: "Montserrat", sans-serif;
    display: flex;
    flex-direction: column;
    align-items: center;
    justify-content: center;
    gap: 40px;
  }
  .card {
    position: relative;
    width: 700px;
    height: 400px;
    border-radius: 26px;
    background: linear-gradient(160deg, var(--card-edge) 0%, var(--card) 55%);
    border-bottom: 7px solid var(--blue-bright);
    border-left: 3px solid var(--blue-bright);
    overflow: hidden;
    box-shadow: 0 14px 30px rgba(0,0,0,0.45);
  }

  /* Front */
  .card-front { display: flex; align-items: center; justify-content: center; }
  .wordmark {
    display: flex;
    align-items: center;
    gap: 16px;
    color: var(--white);
    font-weight: 300;
  }
  .wordmark-dot {
    width: 22px; height: 22px;
    border-radius: 50%;
    background: var(--blue-bright);
  }
  .card-front .wordmark-name { font-size: 40px; letter-spacing: 3px; }

  /* Back */
  .card-back .wordmark { position: absolute; left: 48px; top: 52px; gap: 12px; }
  .card-back .wordmark-dot { width: 16px; height: 16px; }
  .card-back .wordmark-name { font-size: 26px; letter-spacing: 2px; }

  .person {
    position: absolute;
    right: 58px;
    top: 150px;
    text-align: right;
  }
  .person-name { color: var(--blue-bright); font-weight: 700; font-size: 30px; }
  .person-title { color: var(--ice); font-weight: 400; font-size: 16px; margin-top: 2px; }
  .accent-bar {
    position: absolute;
    right: 0;
    top: 146px;
    width: 20px;
    height: 52px;
    background: var(--blue-bright);
  }

  .contact {
    position: absolute;
    left: 48px;
    bottom: 40px;
    color: var(--ice);
    font-weight: 300;
    font-size: 16px;
    line-height: 1.35;
  }
  .address { margin-bottom: 16px; }
  .contact-list { list-style: none; }
  .contact-list li { display: flex; align-items: center; gap: 12px; margin-bottom: 4px; }
  .contact-list svg { width: 16px; height: 16px; fill: var(--blue-bright); flex: none; }
  .abn { margin-top: 8px; }
  .abn-label { color: var(--blue-bright); font-weight: 700; }
</style>
</head>
<body>

<section class="card card-front" aria-label="Card front">
  <div class="wordmark">
    <span class="wordmark-dot"></span>
    <span class="wordmark-name">TBK Plumbing Services</span>
  </div>
</section>

<section class="card card-back" aria-label="Card back">
  <div class="wordmark">
    <span class="wordmark-dot"></span>
    <span class="wordmark-name">TBK Plumbing Services</span>
  </div>

  <div class="person">
    <p class="person-name">Rowan Keddle</p>
    <p class="person-title">Director</p>
  </div>
  <span class="accent-bar"></span>

  <div class="contact">
    <p class="address">24 Harbour Reach Road<br>Fairview, NS 2741</p>
    <ul class="contact-list">
      <li>
        <svg viewBox="0 0 24 24" aria-hidden="true"><path d="M6.6 10.8a15.1 15.1 0 0 0 6.6 6.6l2.2-2.2a1 1 0 0 1 1-.25 11.4 11.4 0 0 0 3.6.57 1 1 0 0 1 1 1V20a1 1 0 0 1-1 1A17 17 0 0 1 3 4a1 1 0 0 1 1-1h3.5a1 1 0 0 1 1 1c0 1.25.2 2.45.57 3.57a1 1 0 0 1-.25 1z"/></svg>
        <span>0431 286 517</span>
      </li>
      <li>
        <svg viewBox="0 0 24 24" aria-hidden="true"><path d="M2 5h20v14H2z M2 5l10 8 10-8" /></svg>
        <span>rowan@tbk-plumbing.com.au</span>
      </li>
      <li>
        <svg viewBox="0 0 24 24" aria-hidden="true"><path d="M12 2a10 10 0 1 0 0 20 10 10 0 0 0 0-20zm6.9 6h-2.9a15.7 15.7 0 0 0-1.4-3.6A8 8 0 0 1 18.9 8zM12 4c.8 1.2 1.5 2.5 1.9 4h-3.8c.4-1.5 1.1-2.8 1.9-4zM4.3 14a8 8 0 0 1 0-4h3.4a16 16 0 0 0 0 4zm.8 2h2.9a15.7 15.7 0 0 0 1.4 3.6A8 8 0 0 1 5.1 16zM8 8H5.1a8 8 0 0 1 4.3-3.6C8.8 5.5 8.3 6.7 8 8zm4 12c-.8-1.2-1.5-2.5-1.9-4h3.8c-.4 1.5-1.1 2.8-1.9 4zm2.3-6H9.7a14.6 14.6 0 0 1 0-4h4.6a14.6 14.6 0 0 1 0 4zm.3 5.6c.6-1.1 1.1-2.3 1.4-3.6h2.9a8 8 0 0 1-4.3 3.6zm1.7-5.6a16 16 0 0 0 0-4h3.4a8 8 0 0 1 0 4z"/></svg>
        <span>www.tbk-plumbing.com.au</span>
      </li>
    </ul>
    <p class="abn"><span class="abn-label">ABN</span> - 73 215 904 386</p>
  </div>
</section>

</body>
</html>
```